New Company Business Card design

Looking for a corporate looking business card utilising my new logo design - the logo i would like embossed as one option and flat as another - simplistic but stylish - less is more - we are an import export business launching into the market - i would like a couple of options as main background - Grey or Black

```html
<!DOCTYPE html>
<html lang="en">
<head>
<meta charset="utf-8">
<title>Harbor Crest Trading – Business Card</title>
<link rel="stylesheet" href="https://fonts.googleapis.com/css2?family=Work+Sans:wght@400;500;600&display=swap">
<style>
  :root {
    --backdrop: #2b2b2b;
    --card: #1c1c1d;
    --card-edge: #262627;
    --emboss-grey: #8a8a8c;
    --brand-blue: #1b7ac8;
    --ink-white: #f2f2f2;
    --divider: #e6e6e6;
  }
  * { box-sizing: border-box; margin: 0; padding: 0; }
  html, body { width: 1200px; height: 900px; overflow: hidden; }
  body {
    background: var(--backdrop);
    font-family: "Work Sans", Arial, sans-serif;
    display: flex;
    flex-direction: column;
    align-items: center;
    justify-content: center;
    gap: 40px;
  }
  .card {
    width: 680px;
    height: 388px;
    background: var(--card);
    border: 1px solid var(--card-edge);
    position: relative;
  }
  .brand {
    display: flex;
    align-items: center;
    gap: 14px;
    font-weight: 500;
    text-transform: uppercase;
    letter-spacing: 0.14em;
    white-space: nowrap;
  }
  .brand-dot { flex: none; border-radius: 50%; }

  /* front: embossed option */
  .card-front { display: flex; align-items: center; justify-content: center; }
  .card-front .brand { color: var(--emboss-grey); font-size: 30px; }
  .card-front .brand-dot { width: 26px; height: 26px; background: var(--emboss-grey); }

  /* back: flat option with details */
  .card-back {
    display: grid;
    grid-template-columns: 400px 1px 1fr;
    align-items: center;
  }
  .card-back .brand {
    justify-self: center;
    color: var(--brand-blue);
    font-size: 22px;
    gap: 10px;
  }
  .card-back .brand-dot { width: 20px; height: 20px; background: var(--brand-blue); }
  .divider { width: 1px; height: 176px; background: var(--divider); }
  .contact { padding-left: 28px; color: var(--ink-white); }
  .contact-name {
    color: var(--brand-blue);
    font-size: 25px;
    font-weight: 600;
    text-transform: uppercase;
    letter-spacing: 0.02em;
  }
  .contact-role { font-size: 16px; margin-bottom: 16px; }
  .contact-address { font-size: 16px; line-height: 1.3; margin-bottom: 10px; font-style: normal; }
  .contact-list { list-style: none; font-size: 16px; line-height: 1.5; }
  .contact-list li { display: flex; align-items: center; gap: 10px; }
  .contact-list svg { width: 12px; height: 12px; flex: none; }
  .web-domain { color: var(--brand-blue); }
</style>
</head>
<body>
  <section class="card card-front" aria-label="Card front">
    <div class="brand"><span class="brand-dot"></span>Harbor Crest Trading</div>
  </section>

  <section class="card card-back" aria-label="Card back">
    <div class="brand"><span class="brand-dot"></span>Harbor Crest Trading</div>
    <div class="divider"></div>
    <div class="contact">
      <p class="contact-name">Daniel Reyes</p>
      <p class="contact-role">Director</p>
      <address class="contact-address">2250 Orchard Valley Rd<br>Larkfield, CA 95410-3381</address>
      <ul class="contact-list">
        <li>
          <svg viewBox="0 0 12 12" aria-hidden="true"><path d="M2.5 1h2l1 3-1.5 1a7 7 0 0 0 3 3l1-1.5 3 1v2A1.5 1.5 0 0 1 9.5 11 8.5 8.5 0 0 1 1 2.5 1.5 1.5 0 0 1 2.5 1z" fill="var(--brand-blue)"/></svg>
          555-204-7716
        </li>
        <li>
          <svg viewBox="0 0 12 12" aria-hidden="true"><rect x="1" y="2.5" width="10" height="7" fill="none" stroke="var(--brand-blue)" stroke-width="1.2"/><path d="M1 2.5l5 4 5-4" fill="none" stroke="var(--brand-blue)" stroke-width="1.2"/></svg>
          info@harborcrest.com
        </li>
        <li>
          <svg viewBox="0 0 12 12" aria-hidden="true"><circle cx="6" cy="6" r="5" fill="none" stroke="var(--brand-blue)" stroke-width="1.1"/><ellipse cx="6" cy="6" rx="2.2" ry="5" fill="none" stroke="var(--brand-blue)" stroke-width="1"/><path d="M1 6h10" stroke="var(--brand-blue)" stroke-width="1"/></svg>
          <span>www.<span class="web-domain">harborcrest</span>.com</span>
        </li>
      </ul>
    </div>
  </section>
</body>
</html>
```